Pharmacy window design

WINDOW DIMENSIONS

4ft 8 1/2" WIDE
7ft 4 1/2" HIGH

i need a window sticker for 4 windows for the outside of a pharmacy. see attached examples. name of the pharmacy is Vista Corner

we would prefer to display products on the window signs eg. Baby care products, medicines. vitamins. fitness. veterinary, Health/ beauty etc.

Target Market(s)

Locals and Tourists

Industry/Entity Type

Pharmacy

```html
<!DOCTYPE html>
<html lang="en">
<head>
<meta charset="utf-8">
<title>Vista Corner Pharmacy – Window Sign</title>
<link rel="stylesheet" href="https://fonts.googleapis.com/css2?family=Oswald:wght@600&family=Montserrat:wght@800&family=Roboto+Condensed:wght@400&display=swap">
<style>
  :root {
    --brand-blue: #3a52a3;
    --brand-green: #78c043;
    --brand-green-soft: #b4df8f;
    --paper: #ffffff;
  }
  html, body {
    margin: 0;
    padding: 0;
    width: 756px;
    height: 1200px;
    overflow: hidden;
    background: var(--paper);
  }
  .window-sign {
    display: block;
    width: 756px;
    height: 1200px;
  }
  .corner-wedge { fill: var(--brand-blue); }
  .brand-name {
    font-family: "Montserrat", sans-serif;
    font-weight: 800;
    font-size: 44px;
    fill: var(--brand-blue);
  }
  .brand-dot { fill: var(--brand-green); }
  .hero-frame {
    fill: none;
    stroke: var(--brand-green);
    stroke-width: 13;
    stroke-linejoin: miter;
  }
  .hero-art { fill: url(#heroGlow); }
  .headline {
    font-family: "Oswald", sans-serif;
    font-weight: 600;
    font-size: 66px;
    fill: var(--brand-blue);
  }
  .range-band { fill: var(--brand-green); }
  .range-primary {
    font-family: "Montserrat", sans-serif;
    font-weight: 800;
    font-size: 36px;
    fill: var(--paper);
  }
  .range-secondary {
    font-family: "Roboto Condensed", sans-serif;
    font-weight: 400;
    font-size: 35px;
    fill: var(--brand-blue);
  }
  .service-frame {
    fill: none;
    stroke: var(--brand-blue);
    stroke-width: 4;
  }
  .service-art { fill: var(--brand-green); }
  .service-label {
    font-family: "Montserrat", sans-serif;
    font-weight: 800;
    font-size: 17px;
    fill: var(--brand-green);
  }
  .divider { stroke: var(--brand-green); stroke-width: 3; }
  .call-line {
    font-family: "Montserrat", sans-serif;
    font-weight: 800;
    font-size: 44px;
    fill: var(--brand-blue);
  }
</style>
</head>
<body>
<svg class="window-sign" viewBox="0 0 756 1200" xmlns="http://www.w3.org/2000/svg">
  <defs>
    <radialGradient id="heroGlow" cx="50%" cy="45%" r="60%">
      <stop offset="0%" stop-color="var(--brand-green)"/>
      <stop offset="70%" stop-color="var(--brand-green)" stop-opacity="0.75"/>
      <stop offset="100%" stop-color="var(--brand-green-soft)" stop-opacity="0.5"/>
    </radialGradient>
  </defs>

  <rect width="756" height="1200" fill="var(--paper)"/>

  <!-- corner wedges -->
  <polygon class="corner-wedge" points="0,0 52,0 181,213 43,437 0,437"/>
  <polygon class="corner-wedge" points="756,0 704,0 575,213 713,437 756,437"/>

  <!-- brand -->
  <g class="brand">
    <circle class="brand-dot" cx="196" cy="82" r="16"/>
    <text class="brand-name" x="226" y="98">Vista Corner</text>
  </g>

  <!-- hero -->
  <polygon class="hero-art" role="img" aria-label="Family illustration: two adults and a child in green silhouette" points="88,437 235,197 523,197 669,437 523,677 235,677"/>
  <polygon class="hero-frame" points="68,437 223,181 535,181 689,437 535,693 223,693"/>

  <!-- headline -->
  <text class="headline" x="378" y="804" text-anchor="middle" textLength="742" lengthAdjust="spacingAndGlyphs">WHERE GOOD HEALTH BEGINS</text>

  <!-- product range -->
  <rect class="range-band" x="0" y="828" width="756" height="52"/>
  <text class="range-primary" x="10" y="867" textLength="738" lengthAdjust="spacingAndGlyphs">HEALTH &amp; BEAUTY,BABY CARE,</text>
  <text class="range-secondary" x="378" y="934" text-anchor="middle" textLength="736" lengthAdjust="spacingAndGlyphs">VETERINARY &amp; FITNESS,VITAMINS &amp; MEDICINES</text>

  <!-- services -->
  <g class="service">
    <polygon class="service-frame" points="16,1026 49,972 113,972 146,1026 113,1080 49,1080"/>
    <circle class="service-art" role="img" aria-label="Medicines icon: capsule and tablet" cx="81" cy="1026" r="32"/>
    <text class="service-label" x="81" y="1104" text-anchor="middle">MEDICINES</text>
  </g>
  <g class="service">
    <polygon class="service-frame" points="216,1026 249,972 313,972 346,1026 313,1080 249,1080"/>
    <circle class="service-art" role="img" aria-label="Vitamins icon: supplement jar" cx="281" cy="1026" r="32"/>
    <text class="service-label" x="281" y="1104" text-anchor="middle">VITAMINS</text>
  </g>
  <g class="service">
    <polygon class="service-frame" points="413,1026 446,972 510,972 543,1026 510,1080 446,1080"/>
    <circle class="service-art" role="img" aria-label="Fitness icon: person on a treadmill" cx="478" cy="1026" r="32"/>
    <text class="service-label" x="478" y="1104" text-anchor="middle">FITNESS</text>
  </g>
  <g class="service">
    <polygon class="service-frame" points="610,1026 643,972 707,972 740,1026 707,1080 643,1080"/>
    <circle class="service-art" role="img" aria-label="Veterinary icon: vet with a dog" cx="675" cy="1026" r="32"/>
    <text class="service-label" x="675" y="1104" text-anchor="middle">VETERINARY</text>
  </g>

  <!-- call to action -->
  <line class="divider" x1="0" y1="1127" x2="756" y2="1127"/>
  <text class="call-line" x="378" y="1185" text-anchor="middle" textLength="722" lengthAdjust="spacing">CALL NOW - 869 555 0148</text>
</svg>
</body>
</html>
```